Real Estate Company Looking for Business Card Designs for 3 Executives

Hello!
Thanks so much for considering our project! We are a real estate investment company located in Edmonton, Alberta called Bellhaven Group of Companies. We invest/develop both commercial and residential real estate and are looking to create 3 DOUBLE-SIDED business cards for 3 top executives in the company! (for some reason it won't let us select the double-sided option, but yes, the cards are double sided and would be happy to tip extra)

We have certain guidelines that we want our business cards to for sure follow - the back of the Business card has to be the Black Background Version of the Logo which has already been designed and linked as a file (first file). We want the entire back of the card to simply just be the black background logo. In terms of the front of the card, would like to see a smaller version of the white background logo (linked as the second file) in the top left hand corner - of course, feel free to get creative and we can make revisions together along the way! and Then after that, just text. We want the card to be sharp, clean, easy on the eyes and highly professional looking. We would like the card to include the Full name of the Company (Bellhaven Group of Companies), Name of the Person, Title, Phone, Email. If possible please provide the front part of the card for 3 people:

1) Bellhaven Group of Companies, Liora Quenby, Chief Financial Officer, 780-555-0142, lioraquenby@bellhavengroup.example

2) Bellhaven Group of Companies, Tobias Quenby, Chief Executive Officer, 780-555-0187, tobiasquenby@bellhavengroup.example

3) Bellhaven Group of Companies, Rui Delcourt, Chief Operations Officer, 587-555-0163, ruidelcourt@bellhavengroup.example

Thank you so much for considering our project & we look forward to seeing your designs!

```html
<!DOCTYPE html>
<html lang="en">
<head>
<meta charset="utf-8">
<title>Bellhaven Business Cards</title>
<link rel="stylesheet" href="https://fonts.googleapis.com/css2?family=Arimo:wght@400;700&display=swap">
<style>
  :root {
    --page: #e6e6e4;
    --card: #2f2f2f;
    --ink: #ffffff;
    --ink-soft: #d9d9d9;
    --rule: #bdbdbd;
    --tree-light: #5a5a5a;
    --tree-dark: #161616;
  }
  * { margin: 0; padding: 0; box-sizing: border-box; }
  html, body { width: 1200px; height: 801px; overflow: hidden; }
  body {
    background: var(--page);
    font-family: "Arimo", Arial, sans-serif;
    color: var(--ink);
    display: flex;
    align-items: center;
    justify-content: center;
    gap: 40px;
  }
  .card {
    position: relative;
    width: 520px;
    height: 297px;
    background: var(--card);
    overflow: hidden;
    box-shadow: 0 6px 18px rgba(0,0,0,0.18);
  }
  .wordmark {
    position: absolute;
    font-weight: 400;
    letter-spacing: 0.45em;
    color: var(--ink);
    white-space: nowrap;
  }

  /* Contact side */
  .card-front .wordmark { top: 58px; right: 34px; font-size: 15px; }
  .card-front .mark-square {
    position: absolute; top: 48px; right: 213px;
    width: 34px; height: 34px; border: 0; background: var(--ink);
  }
  .divider {
    position: absolute; left: 30px; right: 24px; top: 196px;
    height: 1px; background: var(--rule);
  }
  .identity { position: absolute; left: 30px; bottom: 106px; }
  .person-name { font-size: 17px; font-weight: 700; letter-spacing: 0.02em; }
  .person-title { font-size: 13px; color: var(--ink-soft); margin-top: 2px; }
  .contact-list { position: absolute; left: 30px; top: 208px; list-style: none; }
  .contact-list li {
    display: flex; align-items: center; gap: 9px;
    font-size: 13px; color: var(--ink-soft); margin-bottom: 6px;
  }
  .contact-list svg { width: 11px; height: 11px; flex: none; }

  /* Logo side */
  .card-back .wordmark { left: 44px; bottom: 58px; font-size: 20px; }
  .card-back .mark-square {
    position: absolute; left: 44px; bottom: 100px;
    width: 92px; height: 92px; background: var(--ink);
  }
  .forest-art {
    position: absolute; top: 0; right: 0; width: 220px; height: 100%;
    background: linear-gradient(180deg, var(--tree-light) 0%, #333 55%, var(--tree-dark) 100%);
  }
</style>
</head>
<body>
  <section class="card card-front" aria-label="Business card, contact side">
    <span class="mark-square"></span>
    <span class="wordmark">BELLHAVEN</span>
    <div class="identity">
      <p class="person-name">LIORA QUENBY</p>
      <p class="person-title">Chief Financial</p>
    </div>
    <div class="divider"></div>
    <ul class="contact-list">
      <li>
        <svg viewBox="0 0 12 12" aria-hidden="true"><path d="M2.5 1 L4.5 1 L5 3.5 L3.8 4.4 Q5 7 7.6 8.2 L8.5 7 L11 7.5 L11 9.5 Q11 11 9.5 11 Q1 10 1 2.5 Q1 1 2.5 1 Z" fill="#d9d9d9"/></svg>
        780-555-0142
      </li>
      <li>
        <svg viewBox="0 0 12 12" aria-hidden="true"><rect x="0.75" y="2.25" width="10.5" height="7.5" fill="none" stroke="#d9d9d9" stroke-width="1"/><path d="M0.75 2.5 L6 6.5 L11.25 2.5" fill="none" stroke="#d9d9d9" stroke-width="1"/></svg>
        lioraquenby@bellhavengroup.example
      </li>
    </ul>
  </section>

  <section class="card card-back" aria-label="Business card, logo side">
    <div class="forest-art" role="img" aria-label="Embossed illustration of tall pine trees in dark grey tones"></div>
    <span class="mark-square"></span>
    <span class="wordmark">BELLHAVEN</span>
  </section>
</body>
</html>
```